Business Cards for new orthopaedic surgery practice

My husband and I are starting our own orthopaedic surgery practice. We are looking for a business card that is uniform, but one will have my name/title and the other will have his. You can just create one design with my name on it for now. But when I choose your design as the winning design I will ask that you add another copy with his name/title.

We are looking for classy, simple, elite all in one. We like dark blues/a little gold/yellow. Something that goes with our logo. We want our logo incorporated. Here is all the info you need:
Business name: RV Bone & Vitality Center
Location: 38517 North Willowmere Ave
Cedar Brook, FL 34012
Phone: 954-218-4063
Fax: 954-582-7341
Email: info@myrvbonecare.example

Names: Lydia Vance, M.D.
Board Certified Hand and Upper Extremity Surgeon

Ebo Dansu, M.D.
Board Certified Hip & Knee Replacement/General Orthopaedic Surgeon

Can decide what you want to put on the back. Maybe a slogan:
Rooted in Care. Focused on You

I am just going to upload our logo. The only thing is if we select you as the winning design, the location, and phone numbers may change. We will need your help to update that once fully solidified.

Industry/Entity Type

Medical

Contact Information for Business Card

Colors
0054AA
0677BA
7BADD7
CADEEF
E8F1F8
0094D4
00A9DD
6FCCEA
C7EBF8
E9F6FB

Requirements
Must have
• class, appeal,
Should not have
• We want to air on the side of masculine if we are looking at masculine vs. feminine feel. But we still want it classy, sophisticated, and something we will love

```html
<!DOCTYPE html>
<html lang="en">
<head>
<meta charset="utf-8">
<title>RV Bone &amp; Vitality Center – Business Card</title>
<link href="https://fonts.googleapis.com/css2?family=Noto+Serif:wght@400;700&display=swap" rel="stylesheet">
<style>
  :root {
    --navy: #2a3f86;
    --cyan: #1ebfe4;
    --paper: #ffffff;
    --backdrop: #f0f0f1;
  }
  * { box-sizing: border-box; margin: 0; padding: 0; }
  html, body { width: 1200px; height: 990px; overflow: hidden; }
  body {
    background: var(--backdrop);
    font-family: "Noto Serif", Georgia, serif;
    position: relative;
  }
  .card {
    position: absolute;
    left: 245px;
    width: 711px;
    height: 407px;
    background: var(--paper);
    border-radius: 40px;
    border-left: 4px solid var(--cyan);
    border-bottom: 4px solid var(--cyan);
    overflow: hidden;
    box-shadow: 0 14px 22px rgba(0,0,0,0.28);
  }
  .card--front { top: 67px; }
  .card--back { top: 515px; }

  .brand {
    position: absolute;
    color: var(--navy);
    font-weight: 400;
    line-height: 1.15;
    white-space: nowrap;
  }
  .brand--front {
    left: 0; right: 0; top: 148px;
    font-size: 44px;
    text-align: center;
  }
  .brand--back {
    left: 30px; top: 172px;
    width: 290px;
    font-size: 24px;
    text-align: center;
  }
  .divider {
    position: absolute;
    left: 355px; top: 52px;
    width: 1px; height: 272px;
    background: var(--cyan);
  }
  .contact {
    position: absolute;
    left: 424px; top: 64px;
    color: var(--navy);
  }
  .contact__name {
    color: var(--cyan);
    font-weight: 700;
    font-size: 24px;
    letter-spacing: 1px;
    line-height: 1.2;
  }
  .contact__title,
  .contact__address,
  .contact__list {
    font-size: 15.5px;
    line-height: 23px;
  }
  .contact__title { margin-top: 2px; }
  .contact__address { color: var(--cyan); margin-top: 13px; }
  .contact__list { list-style: none; margin-top: 16px; }
  .contact__list li { display: flex; align-items: center; gap: 10px; white-space: nowrap; }
  .contact__list svg { width: 16px; height: 16px; flex: none; }

  .tagline-band {
    position: absolute;
    left: 0; right: 0; top: 348px;
    height: 30px;
    display: flex;
  }
  .tagline-band__main {
    flex: 0 0 570px;
    background: var(--cyan);
    color: #fff;
    font-size: 16px;
    display: flex;
    align-items: center;
    justify-content: center;
    gap: 22px;
    padding-left: 60px;
  }
  .tagline-band__main span::before {
    content: "";
    display: inline-block;
    width: 6px; height: 6px;
    border-radius: 50%;
    background: #fff;
    margin-right: 7px;
    vertical-align: middle;
  }
  .tagline-band__end {
    flex: 1;
    background: var(--navy);
    color: #fff;
    font-size: 10px;
    display: flex;
    align-items: center;
    justify-content: center;
    white-space: nowrap;
  }
</style>
</head>
<body>

<section class="card card--front">
  <h1 class="brand brand--front">RV Bone &amp;<br>Vitality Center</h1>
</section>

<section class="card card--back">
  <p class="brand brand--back">RV Bone &amp;<br>Vitality Center</p>
  <div class="divider"></div>

  <div class="contact">
    <h2 class="contact__name">Lydia Vance, M.D.</h2>
    <p class="contact__title">Board Certified Hand and<br>Upper Extremity Surgeon</p>
    <p class="contact__address">38517 North Willowmere Ave<br>Cedar Brook, FL 34012</p>
    <ul class="contact__list">
      <li>
        <svg viewBox="0 0 24 24" fill="none" stroke="#1ebfe4" stroke-width="2"><path d="M5 3h4l2 5-3 2a12 12 0 0 0 6 6l2-3 5 2v4a2 2 0 0 1-2 2A17 17 0 0 1 3 5a2 2 0 0 1 2-2z"/></svg>
        954-218-4063
      </li>
      <li>
        <svg viewBox="0 0 24 24" fill="none" stroke="#1ebfe4" stroke-width="2"><rect x="3" y="9" width="18" height="12" rx="1"/><path d="M7 9V3h10v6"/><path d="M7 14h2M11 14h2M15 14h2M7 17h2M11 17h2M15 17h2"/></svg>
        954-582-7341
      </li>
      <li>
        <svg viewBox="0 0 24 24" fill="none" stroke="#1ebfe4" stroke-width="2"><circle cx="12" cy="12" r="9"/><path d="M3 12h18M12 3c3 3 3 15 0 18M12 3c-3 3-3 15 0 18"/></svg>
        www.myrvbonecare.example
      </li>
      <li>
        <svg viewBox="0 0 24 24" fill="none" stroke="#1ebfe4" stroke-width="2"><path d="M3 9l9-6 9 6v11H3z"/><path d="M3 9l9 6 9-6"/></svg>
        info@myrvbonecare.example
      </li>
    </ul>
  </div>

  <div class="tagline-band">
    <p class="tagline-band__main"><span>Steady Hands</span><span>Lasting Care</span></p>
    <p class="tagline-band__end">RV Bone &amp; Vitality Center</p>
  </div>
</section>

</body>
</html>
```